Web Design Project for a Software & Consulting Company

We have just completed a recent ArtHerdly project for a new logo (see attached).
As the next stage of our rebranding we now require a website re-design to complement the new logo.
Our current site, http://www.corvinsoft.example was built in-house and does not come across as professional as we would like. We supply software and associated services to some of the world’s largest oil companies and we need our site to reflect that level of client.
We will also be posting another design project for brochures, PowerPoint slides and other materials very soon.
We would like designs for…
Home page
Product page
• TZQ
• BLV
• PNJ
Services
News page
About Us page
Contact Us page
Page for mobile devices that gives basic company and product information
Currently the site is small but we intend to increase content to include white papers etc. this should be taken into account when designing the navigation therefore we would prefer navigation through styled text links rather than images.
Colour schemes should broadly be taken from our new logo, where the dark blue and dark green from the left and right sides of the logo are the main colours, but other, brighter accent colours can be used to highlight sections or content.
Dark Blue = C:88, M:55, Y:44, K:28
Dark Green = C:87, M:53, Y:50, K:50
NB: Don’t use the logo on our current site, make sure you use the one attached.
We would prefer the final file format to be a layered PSD.
The site should be clean and professional and communicate the following...
• That we have a great depth and breadth of knowledge about our customers’ business, enabling us to deliver the best systems and solutions.
• That we are a leading provider of cost estimation and control solutions to the oil and gas industry.
• The benefits of our software and consulting services.
• Show that we deliver outstanding customer service and value with a very high level of professionalism
• The site should have no Flash and be able to self-adjust to fit any screen size.
Things to avoid …
• Obvious and clichéd oil industry imagery, no oil rigs
• Cartoon style graphics
Our Background
We are an integrated software and consulting organization specialising in the drilling side of the oil and gas industry. Simply put our software helps companies better understand, predict and communicate the cost of drilling wells.
We have 3 software products and a consulting offering consisting of…
• TZQ - Probabilistic time and cost software
• BLV – Cost tracking and reporting software
• PNJ – (currently known as DrillSavant) – Lessons learned software
• Consulting services
Our systems are in use in over 30 countries with a broad range of clients including: GN, Marovel, Dunt, Koruna, VELO Sirkami, FALUMI and Quintex.
Our current site can be found at www.corvinsoft.example
Our main competitors are
• http://www.drovanic.example/
• http://www.sumbrask.example/
• http://www.kve.example/services/software-solutions/p1-
Our depth of drilling knowledge, quality of software and collaboration with clients differentiate us form the competition.
We strive for very high levels of customer service.
We look forward to receiving your designs!
Updates
Thanks to all the designers who have submitted a design, we appreciate the effort.
We will do our best to give individual feedback on each design but given that many are quite similar we thought we would give some general feedback first.
Nearly all the designs submitted so far have been slight variations on…
-
Top Menu
-
Scrolling Photo Banner
-
4 Columns
-
Body
-
Deep Footer
These designs are well executed but they are basically the same layout as our existing site and while there is nothing inherently wrong with this layout we would like to see some designs that are a bit more innovative and different. We don’t really want just a polished version of our current site.
Thanks again,
CVS
Thanks to everyone who has submitted a design, the response has been great.
We are close to making a decision so if you are intending to submit a design please do it soon, the deadline is only a few days away.
Thanks again.
CVS
Target Market(s)
Mid to high level executives
Industry/Entity Type
Oil And Gas
Look and feel

```html
<!DOCTYPE html>
<html lang="en">
<head>
<meta charset="utf-8">
<title>Corvinsoft – TZQ Product</title>
<link href="https://fonts.googleapis.com/css2?family=Arimo:wght@400;700&family=PT+Sans:wght@400;700&family=PT+Sans+Narrow:wght@400;700&display=swap" rel="stylesheet">
<style>
:root{
  --teal:#225465;
  --teal-dark:#1b4554;
  --teal-light:#2f6a7c;
  --text:#4a4a4a;
  --ink:#1a1a1a;
  --link:#1387a8;
  --rule:#cfcfcf;
  --white:#ffffff;
  --footer-text:#e3edf0;
}
*{box-sizing:border-box;margin:0;padding:0}
html,body{width:1026px;height:1200px;overflow:hidden;background:var(--white)}
body{font-family:"Arimo",Arial,sans-serif;color:var(--text);position:relative}
.page{position:relative;width:1026px;height:1200px;overflow:hidden}
.abs{position:absolute}

.brand{left:127px;top:40px;display:flex;align-items:center;gap:10px;font-family:"PT Sans",sans-serif;font-weight:700;font-size:26px;color:var(--teal);letter-spacing:1px}
.brand-mark{width:30px;height:30px;border-radius:50%;background:var(--teal)}

.nav{left:440px;top:60px;display:flex;gap:0;font-family:"PT Sans Narrow",sans-serif;font-size:14px;color:#222}
.nav a{display:block;padding:5px 9px;margin-right:13px;color:#222;text-decoration:none;height:27px;line-height:18px}
.nav a.active{background:var(--teal);color:var(--white);border-radius:3px;border:1px solid #123744}

.banner{left:103px;top:133px;width:827px;height:172px;overflow:hidden;background:var(--teal)}
.banner-photo{position:absolute;left:300px;top:0;width:527px;height:172px;
  background:linear-gradient(120deg,#6f8a98 0%,#c9d6de 35%,#eef2f5 60%,#b6c6d2 100%);
  clip-path:polygon(12% 0,100% 0,100% 100%,9% 100%,0 0)}
.banner-title{position:absolute;left:0;top:52px;width:310px;text-align:center;font-family:"PT Sans",sans-serif;font-weight:700;font-size:24px;line-height:33px;color:var(--white)}

.intro-icon{left:103px;top:333px}
.intro-title{left:156px;top:338px;font-family:"PT Sans",sans-serif;font-size:19px;color:var(--teal)}
.copy{left:104px;width:800px;font-size:11px;line-height:15.5px}
.bullets{left:104px;top:500px;list-style:none;font-size:11px}
.bullets li{position:relative;padding-left:18px;height:20px;line-height:16px}
.bullets li::before{content:"";position:absolute;left:2px;top:6px;width:4px;height:4px;border-radius:50%;background:#333}

.section-title{font-family:"PT Sans",sans-serif;font-size:18px;color:var(--teal)}
.rule{height:2px;background:var(--rule)}

.feature-icon{width:38px;height:42px}
.feature-text{width:150px;font-size:10.5px;line-height:17.2px;color:#333}
.feature-text b{color:var(--ink)}
.read-more{font-size:10px;font-weight:700;color:var(--link);display:flex;align-items:center;gap:6px}
.plus{width:11px;height:11px;border-radius:50%;background:#4b4b4b;color:#fff;font-size:10px;line-height:11px;text-align:center}

.thumb{width:89px;height:89px;border:1px solid #d9d9d9;background:#f3f3f3;padding:3px}
.thumb svg{width:81px;height:81px;display:block;background:#fff}

.footer{left:103px;top:957px;width:827px;height:243px;background:linear-gradient(180deg,var(--teal) 0%,var(--teal-light) 100%);color:var(--footer-text)}
.f-head{position:absolute;font-family:"PT Sans Narrow",sans-serif;font-size:15px;color:var(--white);padding-bottom:6px;border-bottom:1px solid #5d8895}
.f-addr{position:absolute;font-family:"PT Sans Narrow",sans-serif;font-size:11.5px;line-height:14.6px}
.f-badge{position:absolute;left:391px;top:50px;width:190px;height:28px;border-radius:3px;background:#3b7282}
.f-touch{position:absolute;left:627px;top:20px;font-family:"PT Sans",sans-serif;font-size:18px;color:var(--white)}
.f-touch-line{position:absolute;left:627px;top:42px;width:155px;height:1px;background:linear-gradient(90deg,#6fc2dc,transparent)}
.field{position:absolute;left:628px;width:171px;background:var(--white);border:1px solid #b8c9cf;border-radius:2px;font-family:"PT Sans Narrow",sans-serif;font-size:12px;color:#333;padding:4px 9px}
.submit{position:absolute;left:744px;top:179px;width:55px;height:21px;background:linear-gradient(#fff,#ddd);border:1px solid #999;font-family:"PT Sans Narrow",sans-serif;font-size:11px;color:#222;text-align:center;line-height:19px}
.f-divider{position:absolute;left:23px;top:125px;width:578px;height:1px;background:#5d8895}
.f-para{position:absolute;left:23px;top:137px;width:560px;font-family:"PT Sans Narrow",sans-serif;font-size:11px;line-height:12.7px}
.f-bottom-rule{position:absolute;left:0;top:215px;width:827px;height:1px;background:#1a3f4c}
.f-links{position:absolute;left:23px;top:225px;font-family:"PT Sans Narrow",sans-serif;font-size:10.5px}
.f-copy{position:absolute;right:27px;top:225px;font-family:"PT Sans Narrow",sans-serif;font-size:10.5px}
</style>
</head>
<body>
<div class="page">

  <div class="abs brand"><span class="brand-mark"></span>CORVINSOFT</div>

  <nav class="abs nav">
    <a href="#">HOME</a>
    <a href="#" class="active">PRODUCTS</a>
    <a href="#">ABOUT US</a>
    <a href="#">NEWS</a>
    <a href="#">SOLUTIONS</a>
    <a href="#">CONTACT US</a>
  </nav>

  <section class="abs banner">
    <div class="banner-photo" role="img" aria-label="Photo of hands typing on a laptop keyboard"></div>
    <h1 class="banner-title">TZQ - Probabilistic<br>time and cost software</h1>
  </section>

  <div class="abs intro-icon" role="img" aria-label="Desktop computer icon">
    <svg width="34" height="32" viewBox="0 0 34 32"><rect x="1" y="3" width="22" height="17" rx="2" fill="#cfd6dc"/><rect x="3" y="5" width="18" height="13" fill="#3d8fd6"/><rect x="8" y="21" width="8" height="4" fill="#9aa4ac"/><rect x="25" y="2" width="8" height="26" rx="1" fill="#b3bbc2"/><rect x="4" y="26" width="18" height="3" fill="#8d969e"/></svg>
  </div>
  <h2 class="abs intro-title">THE BEST TIME AND COST PROBABILISTIC SOFTWARE</h2>

  <p class="abs copy" style="top:386px">Lorem ipsum dolor sit amet, consectetur adipiscing elit. Ut eget augue orci. Quisque accumsan vestibulum massa ac vestibulum.</p>
  <p class="abs copy" style="top:422px">Praesent at est neque. Vivamus felis augue, pharetra molestie pretium non, rutrum sed lorem. Suspendisse eu metus eu nibh fermentum cursus. Etiam in diam risus. Ut pellentesque felis mauris, nec dapibus purus. Fusce id mauris odio. Mauris facilisis ipsum ac nunc vestibulum facilisis. Maecenas vel scelerisque elit. Mauris interdum mauris ut orci tempus cursus. Nam at erat sed nulla consectetur dignissim. Nullam urna leo, congue a lobortis id, elementum et orci. In sed lacinia dolor. Nulla fermentum nisl tellus.</p>
  <ul class="abs bullets">
    <li>Morbi ac ultricies justo.</li>
    <li>Integer id nisi vitae lacus fringilla blandit at non orci.</li>
    <li>Fusce non lacus et dui vulputate laoreet.</li>
  </ul>

  <h2 class="abs section-title" style="left:124px;top:590px">MAIN FEATURES</h2>
  <div class="abs rule" style="left:104px;top:624px;width:467px"></div>
  <h2 class="abs section-title" style="left:620px;top:590px">SOFTWARE FEATURES</h2>
  <div class="abs rule" style="left:596px;top:624px;width:333px"></div>

  <div class="abs feature-icon" style="left:118px;top:652px" role="img" aria-label="Book icon"><svg width="38" height="42"><rect x="4" y="2" width="26" height="36" rx="2" fill="#3a9bd9"/><rect x="4" y="2" width="6" height="36" fill="#1f3e55"/></svg></div>
  <p class="abs feature-text" style="left:171px;top:649px"><b>The point of using Lorem Ipsum</b> is that it has a more-or-less normal distribution of letters, as opposed to using 'Content here, content here', making it look like readable English.</p>
  <a class="abs read-more" style="left:240px;top:772px"><span class="plus">+</span>Read More</a>

  <div class="abs feature-icon" style="left:347px;top:650px" role="img" aria-label="Open box icon"><svg width="40" height="44"><rect x="4" y="12" width="32" height="30" fill="#d07a34"/><rect x="8" y="16" width="24" height="22" fill="#e0934d"/></svg></div>
  <p class="abs feature-text" style="left:408px;top:649px"><b>Many desktop</b> publishing packages and web page editors now use Lorem Ipsum as their default model text, and a search for 'lorem ipsum' will uncover many web sites still in their infancy.</p>
  <a class="abs read-more" style="left:485px;top:772px"><span class="plus">+</span>Read More</a>

  <div class="abs feature-icon" style="left:118px;top:810px" role="img" aria-label="Clipboard icon"><svg width="38" height="42"><rect x="2" y="2" width="30" height="38" rx="2" fill="#c8843c"/><rect x="6" y="6" width="22" height="31" fill="#f4f4f4"/><rect x="11" y="0" width="12" height="5" fill="#9a9a9a"/></svg></div>
  <p class="abs feature-text" style="left:171px;top:807px"><b>Various versions</b> have evolved over the years, sometimes by accident, sometimes on purpose (injected humour and the like).</p>
  <a class="abs read-more" style="left:240px;top:895px"><span class="plus">+</span>Read More</a>

  <div class="abs feature-icon" style="left:353px;top:810px" role="img" aria-label="Help icon"><svg width="38" height="42"><circle cx="19" cy="19" r="17" fill="#3358a8"/><text x="19" y="27" text-anchor="middle" font-family="Arimo,sans-serif" font-weight="700" font-size="22" fill="#fff">?</text></svg></div>
  <p class="abs feature-text" style="left:408px;top:807px"><b>Contrary to popular</b> belief, Lorem Ipsum is not simply random text. It has roots in a piece of classical Latin literature from 45 BC.</p>
  <a class="abs read-more" style="left:483px;top:895px"><span class="plus">+</span>Read More</a>

  <div class="abs thumb" style="left:619px;top:650px"><svg viewBox="0 0 81 81"><rect width="81" height="81" fill="#2b6c8a"/><rect x="4" y="4" width="73" height="10" fill="#f2b600"/><rect x="4" y="18" width="73" height="58" fill="#e8eef3"/><rect x="14" y="52" width="8" height="20" fill="#1f3f7a"/><rect x="24" y="58" width="8" height="14" fill="#1f3f7a"/><rect x="34" y="62" width="8" height="10" fill="#1f3f7a"/></svg></div>
  <div class="abs thumb" style="left:714px;top:650px"><svg viewBox="0 0 81 81"><rect x="10" y="30" width="4" height="14" fill="#2f5fa8"/><rect x="18" y="24" width="4" height="20" fill="#2f5fa8"/><rect x="26" y="34" width="4" height="10" fill="#2f5fa8"/><rect x="34" y="20" width="4" height="24" fill="#2f5fa8"/><rect x="42" y="28" width="4" height="16" fill="#2f5fa8"/><circle cx="16" cy="66" r="9" fill="#d44"/><circle cx="40" cy="66" r="9" fill="#d44"/><circle cx="64" cy="66" r="9" fill="#d44"/><rect x="56" y="18" width="20" height="30" fill="#dde3ea"/></svg></div>
  <div class="abs thumb" style="left:810px;top:650px"><svg viewBox="0 0 81 81"><rect x="4" y="4" width="73" height="7" fill="#f2b600"/><ellipse cx="40" cy="36" rx="30" ry="18" fill="#e3e8ed"/><rect x="30" y="30" width="5" height="16" fill="#e08a00"/><rect x="38" y="24" width="5" height="22" fill="#e08a00"/><rect x="46" y="28" width="5" height="18" fill="#1f3f7a"/><rect x="30" y="58" width="30" height="4" fill="#e08a00"/><rect x="30" y="64" width="22" height="4" fill="#1f3f7a"/></svg></div>
  <div class="abs thumb" style="left:619px;top:747px"><svg viewBox="0 0 81 81"><rect x="4" y="4" width="73" height="4" fill="#2b6c8a"/><circle cx="56" cy="44" r="22" fill="#2a4c72"/><circle cx="56" cy="44" r="17" fill="#e07a3a"/><circle cx="56" cy="44" r="12" fill="#f2f2f2"/><rect x="8" y="56" width="4" height="14" fill="#1f3f7a"/><rect x="14" y="62" width="4" height="8" fill="#e08a00"/></svg></div>
  <div class="abs thumb" style="left:714px;top:747px"><svg viewBox="0 0 81 81"><rect width="81" height="81" fill="#dfe6ee"/><rect x="26" y="10" width="24" height="50" fill="#fff"/><rect x="56" y="30" width="4" height="44" fill="#1f2f8a"/><rect x="62" y="40" width="4" height="34" fill="#1f2f8a"/><rect x="68" y="24" width="4" height="50" fill="#1f2f8a"/><circle cx="30" cy="74" r="10" fill="#7fbf4a"/></svg></div>
  <div class="abs thumb" style="left:810px;top:747px"><svg viewBox="0 0 81 81"><rect x="16" y="36" width="12" height="26" fill="#2a5aa8"/><rect x="32" y="44" width="8" height="18" fill="#2a5aa8"/><rect x="46" y="26" width="10" height="36" fill="#2ea33a"/><rect x="60" y="30" width="10" height="32" fill="#2ea33a"/><line x1="8" y1="62" x2="76" y2="62" stroke="#999"/><line x1="24" y1="8" x2="24" y2="70" stroke="#3ab"/></svg></div>
  <a class="abs read-more" style="left:802px;top:852px"><span class="plus">+</span>view all products</a>

  <footer class="abs footer">
    <h3 class="f-head" style="left:25px;top:20px;width:122px">EUROPE</h3>
    <p class="f-addr" style="left:25px;top:50px">18 Harlow Row<br>Kestrel Bay, KB4 2TR<br>Phone:+44(0)1632 960418<br>Email:eu@corvinsoft.example</p>
    <h3 class="f-head" style="left:199px;top:20px;width:126px">NORTH AMERICA</h3>
    <p class="f-addr" style="left:199px;top:50px">740 Meridan Ave, Suite 210<br>Larkfield, TX 77901<br>Phone:(555) 014 3382<br>Email:us@corvinsoft.example</p>
    <h3 class="f-head" style="left:390px;top:20px;width:195px">OUR GOLD BUSINESS PARTNER</h3>
    <div class="f-badge" aria-label="Partner badge"></div>
    <div class="f-touch">Get in touch</div>
    <div class="f-touch-line"></div>
    <div class="field" style="top:56px;height:23px">Name</div>
    <div class="field" style="top:86px;height:23px">E-mail</div>
    <div class="field" style="top:116px;height:55px">Message</div>
    <div class="submit">SUBMIT</div>
    <div class="f-divider"></div>
    <p class="f-para">Lorem ipsum dolor sit amet, consectetur adipiscing elit. Donec semper nisl eget ante vehicula at viverra est porta. Morbi eleifend, turpis eget vehicula porta, leo velit facilisis justo, quis vehicula velit erat nec est. Pellentesque habitant morbi tristique senectus et netus et malesuada fames ac turpis egestas. Pellentesque consequat est vel metus luctus commodo. In hac habitasse platea dictumst. Suspendisse justo ipsum,</p>
    <div class="f-bottom-rule"></div>
    <div class="f-links">Privacy Policy &nbsp; | &nbsp; Terms &amp; Conditions</div>
    <div class="f-copy">© Copyrights 2012 Corvinsoft</div>
  </footer>

</div>
</body>
</html>
```